Business card design for holistic health care clinic

We need a double-sided business card design for our holistic health care clinic that integrates our logo design and also its color scheme. My business is called Valmira. It is an integrative medicine clinic. You have already done the logo for me. Please ensure an elegant and upscale design that is not cluttered, but still has all the necessary information (please see below for details).

Target Market(s)

Wellness, fitness, rehabilitation for educated, well-traveled open-minded clients who are focused on natural, organic, balanced and preventive healthcare and lifestyle.

Industry/Entity Type

Medical

Contact Information for Business Card

Modern, clean.

Number of Pages Required

1 page

Font styles to use
Serif
Sans Serif

Colors

Designer to choose colors to be used in the design.

Requirements
Must have
• Logo on one side, all other information on the other side.
• Other information should include:
• Tobias Wrenfeld - DOE, CPT, LMT
• 4100 East Marrow Drive
• Austin, TX 78119
• 512 555 0148
• 818 555 0192
• info@ValmiraHealth.example
• t.wrenfeld@ValmiraHealth.example
Nice to have
• Darker background on front - but not totally black - shaded/dark gray.

```html
<!DOCTYPE html>
<html lang="en">
<head>
<meta charset="utf-8">
<title>Valmira – Business Card</title>
<link rel="stylesheet" href="https://fonts.googleapis.com/css2?family=Work+Sans:wght@400;500;600&display=swap">
<style>
  :root {
    --stage: #1f1f20;
    --card: #2a2a2b;
    --blue: #1a96d4;
    --ink: #e4e4e4;
    --emblem-soft: rgba(26, 150, 212, 0.28);
  }
  * { margin: 0; padding: 0; box-sizing: border-box; }
  html, body {
    width: 1200px; height: 930px; overflow: hidden;
    background: var(--stage);
    font-family: "Work Sans", sans-serif;
  }
  .canvas { position: relative; width: 1200px; height: 930px; }
  .card {
    position: absolute; top: 293px;
    width: 540px; height: 309px;
    background: var(--card);
    overflow: hidden;
  }
  .card--front { left: 42px; }
  .card--back { left: 612px; }

  .brand { position: absolute; color: var(--blue); }
  .brand__name {
    font-weight: 600; letter-spacing: 1px; line-height: 1;
  }
  .brand__tagline { font-weight: 500; line-height: 1; margin-top: 6px; }
  .card--front .brand { left: 38px; top: 64px; }
  .card--front .brand__name { font-size: 37px; }
  .card--front .brand__tagline { font-size: 12.5px; }
  .card--back .brand { right: 28px; top: 214px; text-align: center; }
  .card--back .brand__name { font-size: 50px; }
  .card--back .brand__tagline { font-size: 14px; margin-top: 8px; }

  .holder { position: absolute; left: 38px; top: 154px; width: 464px; }
  .holder__name {
    color: var(--blue); font-weight: 600; font-size: 24px;
    letter-spacing: -0.3px; line-height: 1;
  }
  .holder__title { color: var(--ink); font-size: 12.5px; margin-top: 4px; }
  .holder__rule { height: 1px; background: var(--blue); margin-top: 6px; }

  .contact-list {
    position: absolute; left: 38px; top: 219px;
    list-style: none; color: var(--ink); font-size: 13px; line-height: 17px;
  }
  .contact-list li { display: flex; align-items: center; gap: 7px; }
  .contact-list svg { width: 9px; height: 9px; flex: none; }

  .address {
    position: absolute; right: 38px; top: 253px;
    color: var(--ink); font-size: 13px; line-height: 17px;
    text-align: right; font-style: normal;
  }

  .emblem { position: absolute; top: 0; height: 309px; }
  .card--front .emblem {
    left: 300px; width: 240px;
    background: linear-gradient(270deg, var(--emblem-soft), rgba(26,150,212,0.04));
  }
  .card--back .emblem {
    left: 0; width: 243px;
    background: linear-gradient(90deg, var(--emblem-soft), rgba(26,150,212,0.04));
  }
</style>
</head>
<body>
<main class="canvas">

  <section class="card card--front">
    <div class="emblem" role="img" aria-label="Large winged emblem decoration, half shown, continuing across both card sides"></div>

    <div class="brand">
      <div class="brand__name">VALMIRA</div>
      <div class="brand__tagline">Integrative Holistic Medicine</div>
    </div>

    <div class="holder">
      <h1 class="holder__name">TOBIAS WRENFELD</h1>
      <p class="holder__title">DOE, CPT, LMT</p>
      <div class="holder__rule"></div>
    </div>

    <ul class="contact-list">
      <li><svg viewBox="0 0 10 10"><path d="M2 0.5 L4 2.6 L3 3.8 Q4.2 6 6.2 7 L7.4 6 L9.5 8 L8.2 9.5 Q2 8.5 0.5 1.8 Z" fill="var(--blue)"/></svg>512 555 0148</li>
      <li><svg viewBox="0 0 10 10"><rect x="2.5" y="0.5" width="5" height="9" rx="1" fill="none" stroke="var(--blue)" stroke-width="1.2"/></svg>818 555 0192</li>
      <li><svg viewBox="0 0 10 10"><rect x="0.6" y="2" width="8.8" height="6" fill="none" stroke="var(--blue)" stroke-width="1"/><path d="M0.6 2 L5 5.5 L9.4 2" fill="none" stroke="var(--blue)" stroke-width="1"/></svg>info@ValmiraHealth.example</li>
      <li><svg viewBox="0 0 10 10"><circle cx="5" cy="5" r="4.3" fill="none" stroke="var(--blue)" stroke-width="1"/><path d="M0.7 5 H9.3 M5 0.7 Q2.5 5 5 9.3 M5 0.7 Q7.5 5 5 9.3" fill="none" stroke="var(--blue)" stroke-width="0.8"/></svg>t.wrenfeld@ValmiraHealth.example</li>
    </ul>

    <address class="address">4100 East Marrow Drive<br>Austin, TX 78119</address>
  </section>

  <section class="card card--back">
    <div class="emblem" role="img" aria-label="Large winged emblem decoration, half shown, continuing across both card sides"></div>

    <div class="brand">
      <div class="brand__name">VALMIRA</div>
      <div class="brand__tagline">Integrative Holistic Medicine</div>
    </div>
  </section>

</main>
</body>
</html>
```